Classy, Elegant, Simple Business Card Design

Looking to have a classy, simple, and elegant design. Want a top notch designed business card. I really like the look of the new torvane credit card. I also like the design I attached. I am trying to reach 21-29 year old females for booking us for there wedding or event. We offer Disc Jockey Service, Photo Booth Rentals, and Uplighting .

Target Market(s)

21-28 year old females

Contact Information for Business Card

Has to have logo, website, email, and phone number

Font styles to use
Other font styles liked:
• open to font choice, modern, clean
Designer to choose
33a6d7
0791cd
0555a3
ffffff

Requirements
Must have
• Has to have logo, website, email, and phone number
Nice to have
• I really like the design of the new torvane credit card. I also included my logo and some designs I like
Should not have
• clutter or too much info

```html
<!DOCTYPE html>
<html lang="en">
<head>
<meta charset="utf-8">
<title>Brightline Event Group – Business Card</title>
<link rel="stylesheet" href="https://fonts.googleapis.com/css2?family=Questrial&family=Roboto:wght@400;700&display=swap">
<style>
  :root {
    --backdrop: #2e2e30;
    --card-dark: #232326;
    --card-dark-deep: #1b1b1e;
    --brand-blue: #0555a3;
    --brand-blue-bright: #0791cd;
    --brand-sky: #33a6d7;
    --silver: #8c8d91;
    --stripe: #b9bcc2;
    --white: #ffffff;
  }
  * { margin: 0; padding: 0; box-sizing: border-box; }
  html, body { width: 799px; height: 1200px; overflow: hidden; background: var(--backdrop); }
  .canvas {
    position: relative; width: 799px; height: 1200px;
    display: flex; flex-direction: column; align-items: center; justify-content: center; gap: 110px;
  }
  .card {
    position: relative; width: 640px; height: 366px; overflow: hidden;
    border-radius: 4px; box-shadow: 0 18px 40px rgba(0,0,0,.45);
  }
  /* Front */
  .card-front {
    background: linear-gradient(135deg, var(--card-dark) 0%, var(--card-dark-deep) 100%);
    display: flex; align-items: center; justify-content: center;
  }
  .brand-name {
    font-family: "Questrial", sans-serif; font-weight: 400;
    letter-spacing: 4px; text-transform: uppercase; white-space: nowrap;
  }
  .card-front .brand-name { color: var(--silver); font-size: 34px; display: flex; align-items: center; gap: 16px; }
  .brand-dot { width: 18px; height: 18px; border-radius: 50%; background: currentColor; flex: none; }
  /* Back */
  .card-back { background: var(--card-dark); }
  .card-back svg.band { position: absolute; inset: 0; }
  .card-back .brand-name {
    position: absolute; top: 74px; left: 120px; color: var(--white); font-size: 28px;
    display: flex; align-items: center; gap: 14px;
  }
  .holder { position: absolute; left: 34px; top: 256px; font-family: "Roboto", sans-serif; }
  .holder-name { color: var(--brand-blue-bright); font-weight: 700; font-size: 25px; }
  .holder-role { color: var(--white); font-size: 15px; margin-top: 4px; }
  .contacts {
    position: absolute; left: 330px; top: 250px; list-style: none;
    font-family: "Roboto", sans-serif; color: var(--white); font-size: 16px;
  }
  .contacts li { display: flex; align-items: center; gap: 12px; height: 27px; }
  .contacts svg { width: 15px; height: 15px; fill: var(--brand-blue-bright); flex: none; }
</style>
</head>
<body>
<main class="canvas">
  <section class="card card-front" aria-label="Card front">
    <div class="brand-name"><span class="brand-dot"></span>Brightline Event Group</div>
  </section>

  <section class="card card-back" aria-label="Card back">
    <svg class="band" viewBox="0 0 640 366" preserveAspectRatio="none" aria-hidden="true">
      <defs>
        <linearGradient id="blueBand" x1="0" y1="0" x2="1" y2="1">
          <stop offset="0" stop-color="#0a3f7d"/>
          <stop offset="1" stop-color="#1166ad"/>
        </linearGradient>
      </defs>
      <path d="M0 0 H640 V226 C470 170 250 110 0 122 Z" fill="var(--stripe)"/>
      <path d="M0 0 H640 V214 C470 158 250 100 0 112 Z" fill="url(#blueBand)"/>
    </svg>

    <div class="brand-name"><span class="brand-dot"></span>Brightline Event Group</div>

    <div class="holder">
      <p class="holder-name">Evan Marlow</p>
      <p class="holder-role">Founder &amp; CEO</p>
    </div>

    <ul class="contacts">
      <li>
        <svg viewBox="0 0 24 24" aria-hidden="true"><path d="M6.6 10.8a15.1 15.1 0 0 0 6.6 6.6l2.2-2.2a1 1 0 0 1 1-.25 11.4 11.4 0 0 0 3.6.57 1 1 0 0 1 1 1V20a1 1 0 0 1-1 1A17 17 0 0 1 3 4a1 1 0 0 1 1-1h3.5a1 1 0 0 1 1 1c0 1.25.2 2.45.57 3.57a1 1 0 0 1-.25 1z"/></svg>
        555 0142 0187
      </li>
      <li>
        <svg viewBox="0 0 24 24" aria-hidden="true"><path d="M2 5h20v14H2z M3.5 6.5 12 13l8.5-6.5" stroke="#232326" stroke-width="1.5"/></svg>
        evan@brightline-events.com
      </li>
      <li>
        <svg viewBox="0 0 24 24" aria-hidden="true"><circle cx="12" cy="12" r="10"/><path d="M2 12h20M12 2c3 3 3 17 0 20M12 2c-3 3-3 17 0 20" stroke="#232326" stroke-width="1.4" fill="none"/></svg>
        www.brightline-events.com
      </li>
    </ul>
  </section>
</main>
</body>
</html>
```